Black Car Limousine transportation business in Naples Florida

Always stand for my reliability and RVD stands for Love, K and M are the first initials of my children's names. It should show professionalism and a dedication to customer service. We keep our clients identities private. Show our professionalism. We are Black car Black tie company. We service transportation on a reserve basis to and from residents, airports, casinos, hotels,

Target Market(s)

It is a Private car service. High end clients. Businesses, Celebrity and athletes. Service to airports, hotels, special events.

Industry/Entity Type

Business

Contact Information for Business Card

A pearl metallic or Luster card. Standard business card size. Would like the name, Company email, show we take credit cards and phone number. Currently I don't have a website but will like to add later.

Logo Text

STEADFAST RVD TRANSPORTATION

Font styles to use
Serif

Colors
eaeaea
000000

Requirements
Must have
• Must have Company email, show we take credit cards and phone number. Currently I don't have a website but will like to add later.
Nice to have
• Would like to stay with a black and white theme. Open to some color trim.
Should not have
• Open to suggestions

```html
<!DOCTYPE html>
<html lang="en">
<head>
<meta charset="utf-8">
<title>Steadfast RVD Transportation – Business Card</title>
<link rel="stylesheet" href="https://fonts.googleapis.com/css2?family=Bodoni+Moda:opsz,wght@6..96,400;6..96,600;6..96,700&family=Playfair+Display+SC:wght@700&display=swap">
<style>
  :root {
    --card-black: #000000;
    --card-white: #ffffff;
    --gold: #c9a24e;
    --ink: #111111;
    --grey: #5a5a5a;
    --silver: #eaeaea;
  }
  * { box-sizing: border-box; margin: 0; padding: 0; }
  html, body { width: 1200px; height: 344px; overflow: hidden; background: var(--card-white); }
  .card-spread { display: flex; width: 1200px; height: 344px; }
  .card-face { position: relative; width: 600px; height: 344px; text-align: center; }
  .card-front { background: var(--card-black); }
  .card-back { background: var(--card-white); }

  .company-name {
    position: absolute; left: 0; right: 0; top: 70px;
    font-family: "Bodoni Moda", serif;
    font-weight: 600; font-size: 31px; line-height: 38px;
    color: var(--gold);
  }
  .company-name span { display: block; }

  .tagline {
    position: absolute; left: 0; right: 0; top: 203px;
    font-family: "Bodoni Moda", serif; font-weight: 700;
    font-size: 20.5px; color: var(--card-white);
  }
  .front-phone {
    position: absolute; left: 0; right: 0; top: 280px;
    font-family: "Bodoni Moda", serif; font-weight: 700;
    font-size: 23.5px; letter-spacing: 1px; color: var(--silver);
  }

  .owner-name {
    position: absolute; left: 0; right: 0; top: 76px;
    font-family: "Playfair Display SC", serif; font-weight: 700;
    font-size: 28px; letter-spacing: 3px; color: var(--ink);
  }
  .owner-title {
    position: absolute; left: 0; right: 0; top: 114px;
    font-family: "Bodoni Moda", serif; font-weight: 700;
    font-size: 11px; letter-spacing: 1.5px; color: var(--grey);
  }
  .back-phone {
    position: absolute; left: 0; right: 0; top: 200px;
    font-family: "Bodoni Moda", serif; font-weight: 400;
    font-size: 23px; letter-spacing: 1px; color: var(--grey);
  }
  .back-email {
    position: absolute; left: 0; right: 0; top: 236px;
    font-family: "Bodoni Moda", serif; font-weight: 400;
    font-size: 21px; letter-spacing: 3.5px; color: var(--grey);
  }
  .card-note {
    position: absolute; left: 0; right: 0; top: 292px;
    font-family: "Bodoni Moda", serif; font-weight: 600;
    font-size: 11px; letter-spacing: 2.5px; color: var(--grey);
  }
</style>
</head>
<body>
  <main class="card-spread">
    <section class="card-face card-front">
      <h1 class="company-name">
        <span>Steadfast RVD</span>
        <span>Transportation</span>
      </h1>
      <p class="tagline">A black car black tie services</p>
      <p class="front-phone">(877) 555-0142</p>
    </section>
    <section class="card-face card-back">
      <h2 class="owner-name">Marco De Santis</h2>
      <p class="owner-title">PROPRIETOR</p>
      <p class="back-phone">(877) 555-0142</p>
      <p class="back-email">steadfastrvdrides@mail.com</p>
      <p class="card-note">MAJOR CREDIT CARDS ACCEPTED</p>
    </section>
  </main>
</body>
</html>
```